Brightway Haus Inc. Business Card Design

Brightway Haus Inc. is in search of a great clean design for our business cards!

Looking to incorporate our full logo and watermark on side one (however, I am open to having the text and watermark separated within the design.)

On side two, I am looking to have contact information (Name, Position, Phone #, Email, Website (www.thebrightwayhaus.ca). Can have the logo and/or watermark as part of the design if applicable.

Please add tagline "Where Shine Counts" on either side 1 or 2. This tagline can be in a sans serif, serif or cursive font as long as it compliments overall design. Capitalization can be title or sentence case depending on how it fits within the design.

Get creative!! Looking for a clean, crisp, premium design! Looking for a glossy card finish with spot UV features when printed. Cards will also be printed with rounded corners. Standard dimensions (3.5 x 2).

Target Market(s)

B2B - primary clients are business owners or property management corporations. (residential jobs are few and far between)

Industry/Entity Type

Business

Contact Information for Business Card

- clean, crisp design
- double sided
- spot UV accents and glossy finish upon printing
- standard business card size (3.5 x 2) with rounded corners
- please see project description for requirements per side

Font styles to use
Sans Serif

Requirements
Must have
• - adequate bleeds with print ready files
• - cohesive design elements between side 1 & 2
• - spot UV elements (can be on both sides or just one, use your discretion)
• - colour pallet should match the logo file provided
• - incorporate tagline "where shine counts" (this tagline can be in a serif or sans serif font as long as it is complimentary to the overall design.
Nice to have
• - Premium elements with a clean design
Should not have
• - Please omit cartoon or whimsical like designs, think premium.
• - Colours should not stray from the pallet of the provided logo.

```html
<!DOCTYPE html>
<html lang="en">
<head>
<meta charset="utf-8">
<title>Brightway Haus Inc. Business Cards</title>
<link rel="stylesheet" href="https://fonts.googleapis.com/css2?family=Open+Sans:wght@700;800&family=Roboto:wght@400;500&family=Roboto+Condensed:wght@500;700&display=swap">
<style>
  :root {
    --navy: #1b2454;
    --teal: #0db7bb;
    --paper: #f1f1f1;
    --ink: #4a4a4a;
    --white: #ffffff;
    --backdrop: #d6d3cd;
    --rule: #c9c9c9;
  }
  * { margin: 0; padding: 0; box-sizing: border-box; }
  html, body {
    width: 1200px; height: 960px; overflow: hidden;
    background: var(--backdrop);
  }
  .canvas { position: relative; width: 1200px; height: 960px; }

  .card {
    position: absolute; left: 320px; width: 600px;
    border-radius: 18px; overflow: hidden;
    box-shadow: 0 3px 8px rgba(0,0,0,.25);
  }

  /* Side one */
  .card-front { top: 108px; height: 354px; background: var(--navy); }
  .front-brand {
    position: absolute; top: 134px; left: 0; width: 100%;
    text-align: center; color: var(--white);
    font-family: "Open Sans", sans-serif; font-weight: 800;
    font-size: 38px; letter-spacing: -0.5px; line-height: 1;
  }
  .front-tagline {
    position: absolute; top: 194px; left: 0; width: 100%;
    text-align: center; color: var(--white);
    font-family: "Roboto", sans-serif; font-weight: 400;
    font-size: 14px; letter-spacing: 8px; padding-left: 8px;
  }

  /* Side two */
  .card-back { top: 493px; height: 342px; background: var(--paper); }
  .back-waves { position: absolute; inset: 0; }
  .holder { position: absolute; top: 26px; left: 27px; color: var(--white); }
  .holder-name {
    font-family: "Roboto Condensed", sans-serif; font-weight: 700;
    font-size: 20px; line-height: 1.1;
  }
  .holder-title {
    font-family: "Roboto Condensed", sans-serif; font-weight: 500;
    font-size: 14px; margin-top: 6px;
  }
  .back-brand {
    position: absolute; top: 214px; left: 48px; width: 262px;
    color: var(--navy); white-space: nowrap;
    font-family: "Open Sans", sans-serif; font-weight: 800;
    font-size: 21px; letter-spacing: -0.4px; line-height: 1.2;
  }
  .divider {
    position: absolute; left: 325px; top: 152px;
    width: 1px; height: 156px; background: var(--rule);
  }
  .contact {
    position: absolute; left: 356px; top: 157px;
    font-family: "Roboto", sans-serif; font-size: 14px; color: var(--ink);
  }
  .address { line-height: 18px; margin-bottom: 12px; }
  .contact-list { list-style: none; }
  .contact-list li { display: flex; align-items: center; height: 19.4px; }
  .contact-list svg { width: 12px; height: 12px; margin-right: 11px; fill: var(--teal); }
</style>
</head>
<body>
<main class="canvas">

  <section class="card card-front" aria-label="Card side one">
    <div class="front-brand">BRIGHTWAY HAUS INC.</div>
    <div class="front-tagline">Where Shine Counts</div>
  </section>

  <section class="card card-back" aria-label="Card side two">
    <svg class="back-waves" width="600" height="342" viewBox="0 0 600 342" aria-hidden="true">
      <path d="M0 0 H600 V88 C470 40 300 36 170 60 C100 74 40 110 0 150 Z" fill="var(--teal)"/>
      <path d="M0 150 C40 110 100 74 170 60 C300 36 470 40 600 88 V90 C470 52 300 52 180 78 C110 94 45 140 0 208 Z" fill="var(--white)"/>
      <path d="M0 153 C42 113 105 78 175 64 C300 42 470 46 600 89 C470 56 300 58 190 84 C115 102 50 150 0 208 Z" fill="var(--navy)"/>
    </svg>

    <div class="holder">
      <div class="holder-name">MARA ELLISON</div>
      <div class="holder-title">CEO/FOUNDER</div>
    </div>

    <div class="back-brand">BRIGHTWAY HAUS INC.</div>

    <div class="divider"></div>

    <div class="contact">
      <p class="address">214 Lakeview Crescent<br>Kelowna, BC V1Y 2K8</p>
      <ul class="contact-list">
        <li><svg viewBox="0 0 12 12"><path d="M2.5 0.5 L4.5 3 L3.4 4.4 C4.1 6 5.9 7.9 7.6 8.6 L9 7.5 L11.5 9.5 L10.2 11.4 C5.5 11 1 6.5 0.6 1.8 Z"/></svg>250 555 0148</li>
        <li><svg viewBox="0 0 12 12"><path d="M3 0 H9 A1 1 0 0 1 10 1 V11 A1 1 0 0 1 9 12 H3 A1 1 0 0 1 2 11 V1 A1 1 0 0 1 3 0 Z M3.3 1.5 V9.5 H8.7 V1.5 Z"/></svg>250 555 0172</li>
        <li><svg viewBox="0 0 12 12"><path d="M3 0 H9 V3 H3 Z M0.5 4 H11.5 V9 H9.5 V12 H2.5 V9 H0.5 Z M3.5 8 V11 H8.5 V8 Z"/></svg>250 555 0190</li>
        <li><svg viewBox="0 0 12 12"><path d="M0.5 2.5 H11.5 V10 H0.5 Z M1 3 L6 7 L11 3 Z" fill-rule="evenodd"/></svg>hello@thebrightwayhaus.ca</li>
        <li><svg viewBox="0 0 12 12"><circle cx="6" cy="6" r="5.5"/></svg>www.thebrightwayhaus.ca</li>
      </ul>
    </div>
  </section>

</main>
</body>
</html>
```